New Business Card Design Project

Use the flyer uploaded and website www.brightoakbuilders.com for inspiration.
List Our Services on Backside of business cards
Marcus Delling
Harborline Builders Inc.
Licensed General Contractors
858-471-6093

Contact Information for Business Card

Use the flyer uploaded and website www.brightoakbuilders.com for inspiration. List Our Services on Backside of business cards Marcus Delling Harborline Builders Inc. Licensed General Contractors 858-471-6093

```html
<!DOCTYPE html>
<html lang="en">
<head>
<meta charset="utf-8">
<title>Harborline Builders – Business Card</title>
<link href="https://fonts.googleapis.com/css2?family=Poppins:wght@300;400;500&display=swap" rel="stylesheet">
<style>
  :root {
    --page-bg: #e4e4e2;
    --card-bg: #2e2e2c;
    --ink: #f2f2ef;
    --ink-soft: #d9d9d5;
    --rule: #bdbdb8;
  }
  * { box-sizing: border-box; margin: 0; padding: 0; }
  html, body { width: 1200px; height: 900px; overflow: hidden; }
  body {
    background: var(--page-bg);
    font-family: "Poppins", sans-serif;
    color: var(--ink);
    position: relative;
  }
  .card {
    position: absolute;
    left: 320px;
    width: 560px;
    height: 320px;
    background: var(--card-bg);
    box-shadow: 0 10px 24px rgba(0,0,0,0.18);
  }
  .card--front { top: 100px; }
  .card--back { top: 480px; }

  /* Front */
  .brand {
    position: absolute;
    left: 40px; top: 0; bottom: 0; width: 220px;
    display: flex; align-items: center; justify-content: center; gap: 10px;
  }
  .brand__mark { width: 10px; height: 10px; border: 1px solid var(--ink); flex: none; }
  .brand__name { font-size: 15px; font-weight: 300; letter-spacing: 1.5px; text-transform: uppercase; }
  .divider-v {
    position: absolute; left: 286px; top: 112px; width: 1px; height: 96px; background: var(--rule);
  }
  .contact { position: absolute; left: 318px; top: 108px; }
  .contact__name { font-size: 24px; font-weight: 400; letter-spacing: 1px; text-transform: uppercase; line-height: 1.1; }
  .contact__line { font-size: 12.5px; font-weight: 300; line-height: 1.35; color: var(--ink-soft); }
  .contact__phone { display: flex; align-items: center; gap: 8px; margin-top: 18px; font-size: 13px; font-weight: 300; }
  .contact__phone svg { width: 11px; height: 11px; fill: var(--ink); }

  /* Back */
  .guarantee {
    position: absolute; left: 40px; right: 40px; top: 34px;
    text-align: center; font-size: 20px; font-weight: 400; letter-spacing: 0.5px; text-transform: uppercase;
  }
  .guarantee-rule { position: absolute; left: 50px; right: 50px; top: 72px; height: 1px; background: var(--rule); }
  .specialty-tag {
    position: absolute; left: 50%; top: 88px; transform: translateX(-50%);
    border: 1px solid var(--ink); padding: 3px 14px;
    font-size: 17px; font-weight: 400; letter-spacing: 1px; text-transform: uppercase; white-space: nowrap;
  }
  .services { position: absolute; top: 142px; list-style: none; }
  .services--left { left: 48px; }
  .services--right { left: 300px; }
  .services li { display: flex; align-items: flex-start; gap: 8px; font-size: 12px; font-weight: 300; line-height: 1.35; margin-bottom: 8px; }
  .services svg { width: 11px; height: 11px; flex: none; margin-top: 3px; }
  .services-divider { position: absolute; left: 282px; top: 140px; width: 1px; height: 126px; background: var(--rule); }
</style>
</head>
<body>
  <section class="card card--front" aria-label="Business card front">
    <div class="brand">
      <span class="brand__mark"></span>
      <span class="brand__name">Harborline Builders</span>
    </div>
    <div class="divider-v"></div>
    <div class="contact">
      <p class="contact__name">Marcus Delling</p>
      <p class="contact__line">Harborline Builders Inc.</p>
      <p class="contact__line">Licensed General Contractors</p>
      <p class="contact__phone">
        <svg viewBox="0 0 24 24" aria-hidden="true"><path d="M6.6 10.8a15.1 15.1 0 0 0 6.6 6.6l2.2-2.2a1 1 0 0 1 1-.25 11.4 11.4 0 0 0 3.6.57 1 1 0 0 1 1 1V20a1 1 0 0 1-1 1A17 17 0 0 1 3 4a1 1 0 0 1 1-1h3.5a1 1 0 0 1 1 1c0 1.25.2 2.45.57 3.57a1 1 0 0 1-.25 1z"/></svg>
        858-471-6093
      </p>
    </div>
  </section>

  <section class="card card--back" aria-label="Business card back">
    <p class="guarantee">Our Services Are 100% Guaranteed</p>
    <div class="guarantee-rule"></div>
    <p class="specialty-tag">Specializing In:</p>

    <ul class="services services--left">
      <li><svg viewBox="0 0 12 12" aria-hidden="true"><rect x="0.5" y="0.5" width="11" height="11" fill="none" stroke="#f2f2ef"/><path d="M3 6.2l2 2 4-4.4" fill="none" stroke="#f2f2ef" stroke-width="1.2"/></svg>Remodel: Kitchen &amp; Bath</li>
      <li><svg viewBox="0 0 12 12" aria-hidden="true"><rect x="0.5" y="0.5" width="11" height="11" fill="none" stroke="#f2f2ef"/><path d="M3 6.2l2 2 4-4.4" fill="none" stroke="#f2f2ef" stroke-width="1.2"/></svg>Painting: Interior &amp; Exterior</li>
      <li><svg viewBox="0 0 12 12" aria-hidden="true"><rect x="0.5" y="0.5" width="11" height="11" fill="none" stroke="#f2f2ef"/><path d="M3 6.2l2 2 4-4.4" fill="none" stroke="#f2f2ef" stroke-width="1.2"/></svg>Flooring: Carpet, Vinyl, Wood</li>
      <li><svg viewBox="0 0 12 12" aria-hidden="true"><rect x="0.5" y="0.5" width="11" height="11" fill="none" stroke="#f2f2ef"/><path d="M3 6.2l2 2 4-4.4" fill="none" stroke="#f2f2ef" stroke-width="1.2"/></svg>Window &amp; Door Replacement</li>
    </ul>
    <div class="services-divider"></div>
    <ul class="services services--right">
      <li><svg viewBox="0 0 12 12" aria-hidden="true"><rect x="0.5" y="0.5" width="11" height="11" fill="none" stroke="#f2f2ef"/><path d="M3 6.2l2 2 4-4.4" fill="none" stroke="#f2f2ef" stroke-width="1.2"/></svg>Plumbing: Repairs &amp; Upgrades</li>
      <li><svg viewBox="0 0 12 12" aria-hidden="true"><rect x="0.5" y="0.5" width="11" height="11" fill="none" stroke="#f2f2ef"/><path d="M3 6.2l2 2 4-4.4" fill="none" stroke="#f2f2ef" stroke-width="1.2"/></svg><span>Energy-Efficient Upgrades Deck<br>&amp; Patio Construction</span></li>
      <li><svg viewBox="0 0 12 12" aria-hidden="true"><rect x="0.5" y="0.5" width="11" height="11" fill="none" stroke="#f2f2ef"/><path d="M3 6.2l2 2 4-4.4" fill="none" stroke="#f2f2ef" stroke-width="1.2"/></svg>Water &amp; Mold Damage</li>
      <li><svg viewBox="0 0 12 12" aria-hidden="true"><rect x="0.5" y="0.5" width="11" height="11" fill="none" stroke="#f2f2ef"/><path d="M3 6.2l2 2 4-4.4" fill="none" stroke="#f2f2ef" stroke-width="1.2"/></svg>Garage Renovation</li>
    </ul>
  </section>
</body>
</html>
```